Business card design for my company.
I would like the card's background colour to be black. You can also see our web site to get an idea of our brand. https://www.tmwhomecrafting.com.au/
- Name
- Email

```html
<!DOCTYPE html>
<html lang="en">
<head>
<meta charset="utf-8">
<title>TMW Home Crafting – Business Card</title>
<link rel="stylesheet" href="https://fonts.googleapis.com/css2?family=Montserrat:wght@400;500;700&display=swap">
<style>
  :root {
    --stage: #2b2b2d;
    --card: #141414;
    --white: #f4f4f4;
    --green: #1e9e4a;
    --muted: #e6e6e6;
  }
  * { box-sizing: border-box; margin: 0; padding: 0; }
  html, body {
    width: 1200px; height: 900px; overflow: hidden;
    background: var(--stage);
    font-family: "Montserrat", Arial, sans-serif;
  }
  .stage {
    width: 1200px; height: 900px;
    display: flex; flex-direction: column; align-items: center; justify-content: center;
    gap: 48px;
  }
  .card {
    width: 680px; height: 388px;
    background: var(--card);
    border-radius: 26px;
    position: relative;
    box-shadow: 0 14px 30px rgba(0,0,0,.45);
  }
  .brand { display: flex; align-items: center; gap: 14px; }
  .brand-mark { width: 18px; height: 18px; background: var(--green); flex: none; }
  .brand-name {
    color: var(--white); font-weight: 700; letter-spacing: .04em;
    text-transform: uppercase; line-height: 1.15;
  }
  /* front */
  .card-front { display: flex; align-items: center; justify-content: center; }
  .card-front .brand-name { font-size: 40px; }
  .card-front .brand-mark { width: 26px; height: 26px; }
  /* back */
  .card-back { display: flex; align-items: center; padding: 0 46px; }
  .card-back .brand { width: 250px; }
  .card-back .brand-name { font-size: 26px; }
  .divider { width: 2px; height: 200px; background: var(--green); margin: 0 34px 0 22px; flex: none; }
  .details { color: var(--muted); }
  .person-name { color: var(--green); font-weight: 700; font-size: 30px; }
  .person-role { font-size: 16px; margin-top: 2px; }
  .location { font-size: 16px; margin-top: 18px; }
  .contacts { list-style: none; margin-top: 12px; font-size: 16px; }
  .contacts li { display: flex; align-items: center; gap: 10px; line-height: 1.6; }
  .contacts svg { width: 14px; height: 14px; flex: none; }
</style>
</head>
<body>
<main class="stage">
  <section class="card card-front" aria-label="Card front">
    <div class="brand">
      <span class="brand-mark"></span>
      <span class="brand-name">TMW Home Crafting</span>
    </div>
  </section>

  <section class="card card-back" aria-label="Card back">
    <div class="brand">
      <span class="brand-mark"></span>
      <span class="brand-name">TMW Home<br>Crafting</span>
    </div>
    <div class="divider"></div>
    <div class="details">
      <p class="person-name">Lachlan Reeve</p>
      <p class="person-role">General Manager</p>
      <p class="location">Riverton, Tasmania, Australia</p>
      <ul class="contacts">
        <li>
          <svg viewBox="0 0 16 16" aria-hidden="true"><path fill="#1e9e4a" d="M3 1h3l1.5 4-2 1.2a9 9 0 0 0 4.3 4.3L11 8.5l4 1.5v3a2 2 0 0 1-2 2A12 12 0 0 1 1 3a2 2 0 0 1 2-2z"/></svg>
          0400 555 018
        </li>
        <li>
          <svg viewBox="0 0 16 16" aria-hidden="true"><rect x="1" y="3" width="14" height="10" fill="#1e9e4a"/><path d="M1 3l7 6 7-6" fill="none" stroke="#141414" stroke-width="1.4"/></svg>
          info@tmwhomecrafting.com.au
        </li>
        <li>
          <svg viewBox="0 0 16 16" aria-hidden="true"><circle cx="8" cy="8" r="7" fill="none" stroke="#1e9e4a" stroke-width="1.6"/><ellipse cx="8" cy="8" rx="3" ry="7" fill="none" stroke="#1e9e4a" stroke-width="1.2"/><path d="M1 8h14" stroke="#1e9e4a" stroke-width="1.2"/></svg>
          www.tmwhomecrafting.com.au
        </li>
      </ul>
    </div>
  </section>
</main>
</body>
</html>
```